New Business Card Design

We would like to refresh our business cards and make them look better. We are an IT company specialising in Cloud Services, IT Managed Services, software and hardware. I have attached a PSD of our current design. Also attached our logo.
Updates

I have uploaded all new logos in EPS format.

Can you please edit all designs to include a job title for Marcus Hollis, eg. General Manager

Industry/Entity Type

Software

Colors
ffffff

Requirements
Must have
• Please use white background.
Should not have
• Black background

```html
<!DOCTYPE html>
<html lang="en">
<head>
<meta charset="utf-8">
<title>Meridian Technology – Business Card</title>
<link rel="stylesheet" href="https://fonts.googleapis.com/css2?family=Jost:wght@400;500;700&display=swap">
<style>
  :root {
    --backdrop: #e6e7e9;
    --card: #ffffff;
    --accent: #b9432b;
    --ink: #2f3236;
  }
  * { box-sizing: border-box; margin: 0; padding: 0; }
  html, body { width: 1200px; height: 1200px; overflow: hidden; }
  body {
    background: var(--backdrop);
    font-family: "Jost", sans-serif;
    display: flex;
    flex-direction: column;
    align-items: center;
    justify-content: center;
    gap: 60px;
  }
  .card {
    width: 900px;
    height: 500px;
    background: var(--card);
    box-shadow: 0 8px 24px rgba(0,0,0,0.12);
    position: relative;
  }
  .brand-name {
    color: var(--ink);
    font-weight: 500;
    letter-spacing: 0;
    white-space: nowrap;
  }

  /* Front */
  .card-front .brand-name {
    position: absolute;
    left: 0; width: 470px; top: 0; height: 100%;
    display: flex;
    align-items: center;
    justify-content: center;
    font-size: 30px;
  }
  .divider {
    position: absolute;
    left: 470px; top: 95px;
    width: 2px; height: 310px;
    background: var(--accent);
  }
  .contact {
    position: absolute;
    left: 530px; top: 120px;
  }
  .contact-name {
    font-size: 34px;
    font-weight: 700;
    color: var(--ink);
    line-height: 1.1;
  }
  .contact-role {
    font-size: 18px;
    color: var(--accent);
    margin-top: 4px;
    margin-bottom: 28px;
  }
  .contact-list { list-style: none; }
  .contact-list li {
    display: flex;
    align-items: center;
    gap: 16px;
    font-size: 22px;
    color: var(--ink);
    height: 40px;
  }
  .contact-list svg { width: 20px; height: 20px; flex: none; }

  /* Back */
  .card-back .brand-name {
    position: absolute;
    left: 0; right: 0; top: 0; height: 380px;
    display: flex;
    align-items: center;
    justify-content: center;
    font-size: 48px;
  }
  .tagline {
    position: absolute;
    left: 0; right: 0; bottom: 70px;
    display: flex;
    align-items: center;
    gap: 20px;
    color: var(--accent);
    font-size: 26px;
    letter-spacing: 0.03em;
  }
  .tagline-rule { flex: 1; height: 2px; background: var(--accent); }
</style>
</head>
<body>

  <section class="card card-front">
    <div class="brand-name">Meridian Technology</div>
    <div class="divider"></div>
    <div class="contact">
      <div class="contact-name">Marcus Hollis</div>
      <div class="contact-role">General Manager</div>
      <ul class="contact-list">
        <li>
          <svg viewBox="0 0 20 20" aria-hidden="true"><path fill="var(--accent)" d="M4 2l4 1 1 4-2 2c1 2 3 4 5 5l2-2 4 1 1 4-2 2C9 19 1 11 2 4z"/></svg>
          07 3555 0148
        </li>
        <li>
          <svg viewBox="0 0 20 20" aria-hidden="true"><rect x="5" y="1" width="10" height="18" rx="2" fill="var(--accent)"/><rect x="7" y="4" width="6" height="9" fill="#fff"/><circle cx="10" cy="16" r="1.2" fill="#fff"/></svg>
          0400 555 217
        </li>
        <li>
          <svg viewBox="0 0 20 20" aria-hidden="true"><rect x="1" y="4" width="18" height="12" fill="var(--accent)"/><path d="M1 4l9 7 9-7" fill="none" stroke="#fff" stroke-width="1.5"/></svg>
          mhollis@meridianit.com.au
        </li>
        <li>
          <svg viewBox="0 0 20 20" aria-hidden="true" fill="none" stroke="var(--accent)" stroke-width="1.5"><circle cx="10" cy="10" r="8"/><ellipse cx="10" cy="10" rx="3.5" ry="8"/><path d="M2 10h16M3.5 6h13M3.5 14h13"/></svg>
          www.meridianit.com.au
        </li>
      </ul>
    </div>
  </section>

  <section class="card card-back">
    <div class="brand-name">Meridian Technology</div>
    <div class="tagline">
      <span class="tagline-rule"></span>
      <span>IT SERVICES • SOLUTIONS • SUPPORT</span>
      <span class="tagline-rule"></span>
    </div>
  </section>

</body>
</html>
```